PSD Designs needed to give to my Developer

Hello, I need PSD files to give to my programmer for the creation of my new website. The website is for KORVA lane, a new clothing company based in Chicago, IL. We sell womens, mens and kids fashion. We specialize in jackets, outerwear and sweaters, but we sell clothing from every category, I have someone working on the logo, so I can't include it for reference. However, I have included 2 reference sites as well as a PDF of how the 2 reference sites could be merged together. The main company color should be blue (hence the name KORVA lane), and the overall feel of the site should be FUN. It should communicate: This is where you want to shop if you want a FUN, HAPPY experience. I need the Home Page file designed very quickly. Whoever is awarded this job will immediately continue working with me to design the other 8 pages. I will pay for all pages. The amount I am offering is for this one page only, and I will pay you additional to design all other 8 pages. Thank you for your time and I will be picking the best design so that we can immediately build a great relationship and work through the rest of the project.

Industry/Entity Type

Apparel Store

Number of Pages Required

1 page

Font styles to use
Sans Serif

Colors
33a6d7
0492cd
ffffff

Requirements
Must have
• I have included all notes in the project description so please check there. My project must communicate: Fun and Happy Design. Even tho I have chosen a few variations of blue below, I still want the designer to incorporate other colors as necessary to acheive the desired look.
Should not have
• It should have a boring, childish feel

```html
<!DOCTYPE html>
<html lang="en">
<head>
<meta charset="utf-8">
<title>KORVA lane — Home</title>
<link rel="stylesheet" href="https://fonts.googleapis.com/css2?family=Antonio:wght@400&family=Arimo:wght@700&display=swap">
<style>
  :root {
    --blue: #0099cc;
    --blue-deep: #0492cd;
    --blue-soft: #33a6d7;
    --white: #ffffff;
    --page-top: #e9f3f6;
    --page-bottom: #d4ecef;
    --glow: rgba(120, 205, 210, 0.55);
    --knit-grey: #9a9a9c;
    --knit-navy: #2c3550;
    --knit-black: #1f1f22;
    --knit-red: #c4475a;
    --knit-olive: #5e6250;
  }
  * { box-sizing: border-box; margin: 0; padding: 0; }
  html, body { width: 1200px; height: 1000px; overflow: hidden; }
  body {
    position: relative;
    font-family: "Arimo", Arial, sans-serif;
    font-weight: 700;
    background: linear-gradient(180deg, var(--page-top) 0%, #f4f9fa 45%, var(--page-bottom) 100%);
  }
  a { text-decoration: none; }
  .backdrop {
    position: absolute; inset: 0;
    background:
      radial-gradient(ellipse at 30% 20%, rgba(200,215,220,0.5), transparent 60%),
      radial-gradient(ellipse at 80% 60%, rgba(190,225,230,0.5), transparent 60%);
  }

  /* Promo bar */
  .promo-bar {
    position: absolute; left: 29px; top: 14px; width: 1139px; height: 43px;
    background: var(--blue); color: var(--white);
    display: flex; align-items: center;
  }
  .promo-text { position: absolute; left: 11px; font-size: 20px; }
  .stylist-login { position: absolute; left: 797px; font-size: 18px; }
  .social { position: absolute; left: 958px; display: flex; gap: 8px; }
  .social span { width: 30px; height: 30px; border-radius: 4px; background: var(--white); display: block; }

  /* Main navigation */
  .main-nav a {
    position: absolute; top: 102px; font-size: 17px; color: var(--blue-deep); white-space: nowrap;
  }
  .main-nav a.current::after {
    content: ""; position: absolute; left: 0; right: 0; top: 24px; height: 4px; background: var(--blue-deep);
  }
  .brand {
    position: absolute; left: 780px; top: 74px; width: 380px;
    text-align: center; font-size: 41px; line-height: 54px; color: var(--blue-deep);
  }

  /* Display type */
  .display {
    display: inline-block; flex: none;
    font-family: "Antonio", "Arial Narrow", sans-serif; font-weight: 400;
    color: var(--white); text-transform: uppercase; white-space: nowrap;
    letter-spacing: 2px;
    transform: scaleX(0.58);
    text-shadow:
      2px 0 0 var(--blue-deep), -2px 0 0 var(--blue-deep),
      0 2px 0 var(--blue-deep), 0 -2px 0 var(--blue-deep),
      1.5px 1.5px 0 var(--blue-deep), -1.5px -1.5px 0 var(--blue-deep),
      1.5px -1.5px 0 var(--blue-deep), -1.5px 1.5px 0 var(--blue-deep);
  }

  .knit {
    background: linear-gradient(135deg,
      var(--knit-grey) 0 22%, var(--knit-navy) 22% 38%, var(--knit-black) 38% 52%,
      var(--knit-red) 52% 70%, var(--knit-olive) 70% 100%);
  }

  /* Hero */
  .hero-circle {
    position: absolute; left: 72px; top: 137px; width: 366px; height: 366px; border-radius: 50%;
    box-shadow: 0 0 30px 14px var(--glow);
    display: flex; align-items: center; justify-content: center;
  }
  .hero-circle .display { font-size: 116px; line-height: 1; word-spacing: 14px; margin-top: -12px; }

  .hero-banner {
    position: absolute; left: 521px; top: 217px; width: 544px; height: 220px; border-radius: 8px;
    box-shadow: 0 0 30px 12px var(--glow);
    background: linear-gradient(110deg,
      #a7a7a9 0 30%, #6f7482 30% 50%, #4b5266 50% 66%, #3a3a3e 66% 80%, var(--knit-red) 80% 100%);
    display: flex; flex-direction: column; align-items: center;
  }
  .hero-banner .headline { font-size: 112px; line-height: 1; margin-top: 34px; }
  .hero-banner .sub { font-size: 33px; line-height: 1; margin-top: 8px; letter-spacing: 1px; transform: scaleX(0.66); }

  .slider-dots { position: absolute; left: 578px; top: 474px; display: flex; gap: 9px; }
  .slider-dots span {
    width: 13px; height: 13px; border-radius: 50%; border: 2px solid var(--blue-soft); background: var(--white);
  }
  .slider-dots span.active { background: radial-gradient(circle, var(--blue-soft) 0 35%, var(--white) 40%); }

  /* Feature tiles */
  .tile {
    position: absolute; border-radius: 8px; overflow: hidden;
    box-shadow: 0 0 24px 8px var(--glow);
    display: flex; align-items: center; justify-content: center;
  }
  .tile-story {
    left: 23px; top: 513px; width: 577px; height: 192px;
    background: linear-gradient(180deg, #3b4156 0 18%, var(--knit-red) 18% 45%, #8a8e86 45% 70%, var(--knit-olive) 70% 100%);
  }
  .tile-shop {
    left: 611px; top: 513px; width: 577px; height: 192px;
    background: linear-gradient(160deg, #d9d9d9 0 12%, #9a6a3c 12% 24%, #36405a 24% 48%, #69738a 48% 70%, #dedede 70% 100%);
  }
  .tile-story .display, .tile-shop .display { font-size: 150px; line-height: 1; margin-top: 6px; }
  .tile-join {
    left: 23px; top: 732px; width: 1165px; height: 190px;
    background: linear-gradient(90deg, #bfc9cf 0%, #4b4f57 30%, #6a5a55 50%, #3d3c44 72%, #c9c4bd 100%);
    align-items: flex-end;
  }
  .tile-join .display { font-size: 124px; line-height: 1; margin-bottom: 6px; }

  /* Footer */
  .footer-nav a {
    position: absolute; top: 941px; font-size: 17px; color: var(--blue-deep); white-space: nowrap;
  }
  .copyright {
    position: absolute; top: 969px; left: 0; width: 1318px; text-align: center;
    font-size: 16px; color: var(--blue-deep);
  }
</style>
</head>
<body>
  <div class="backdrop" role="img" aria-label="Faded photo of a shopping mall interior"></div>

  <header>
    <div class="promo-bar">
      <span class="promo-text">Pop-up your own KORVA Boulevard for ONLY $99</span>
      <span class="stylist-login">Stylist Login</span>
      <div class="social" aria-label="Social media links">
        <span aria-label="Social link 1"></span>
        <span aria-label="Social link 2"></span>
        <span aria-label="Social link 3"></span>
        <span aria-label="Social link 4"></span>
      </div>
    </div>

    <nav class="main-nav">
      <a class="current" href="#" style="left:32px">HOME</a>
      <a href="#" style="left:104px">GET TO KNOW US</a>
      <a href="#" style="left:280px">WHY KORVA?</a>
      <a href="#" style="left:414px">HOST A POP-UP</a>
      <a href="#" style="left:583px">BECOME A STYLIST</a>
    </nav>

    <div class="brand">KORVA lane logo<br>here</div>
  </header>

  <main>
    <a class="hero-circle knit" href="#" role="img" aria-label="Photo of folded knit sweaters in grey, navy, black, red and olive">
      <span class="display">Shop Now</span>
    </a>

    <div class="hero-banner" role="img" aria-label="Photo of stacked knit sweaters">
      <span class="display headline">Limited Inventory</span>
      <span class="display sub">That's only available for ONE week!</span>
    </div>

    <div class="slider-dots">
      <span></span><span class="active"></span><span></span><span></span>
    </div>

    <a class="tile tile-story" href="#" role="img" aria-label="Photo of a stack of folded sweaters">
      <span class="display">Our Story</span>
    </a>
    <a class="tile tile-shop" href="#" role="img" aria-label="Photo of sweaters hanging on wooden hangers">
      <span class="display">Shop</span>
    </a>
    <a class="tile tile-join" href="#" role="img" aria-label="Photo of three smiling friends in beanies">
      <span class="display">Be Happier, Join the Mouvement</span>
    </a>
  </main>

  <footer>
    <nav class="footer-nav">
      <a href="#" style="left:246px">HOME</a>
      <a href="#" style="left:319px">GET TO KNOW US</a>
      <a href="#" style="left:496px">WHY KORVA?</a>
      <a href="#" style="left:629px">HOST A POP-UP</a>
      <a href="#" style="left:797px">BECOME A STYLIST</a>
    </nav>
    <p class="copyright">© 2018 KORVA lane Chicago IL. All Rights Reserve</p>
  </footer>
</body>
</html>
```